American cannabis tech company business card design

Pavrel.com is seeking a modern, professional, and brand-aligned business card that represents our company and its core values: Mission, Story, Values, and Impact. As an innovative cannabis company, we want a business card that is not only visually appealing but also serves as a representation of who we are and what we stand for.

Project Scope: Design a double-sided business card that integrates our brand identity and core values. Incorporate our key brand elements, ensuring a sleek and contemporary aesthetic. Visually reflect our core values (Mission, Story, Values, Impact) in a way that is engaging yet professional.

Target Market(s)

Vendors, third parties,

Contact Information for Business Card

Contact details (name, title, email, phone, website, etc.)

Font styles to use
Other font styles liked:
• Caslon, Centra

Colors

Designer to choose colors to be used in the design.

Requirements
Must have
• Pavrel.com logo and branding A creative yet clean way to integrate our core values (Mission, Story, Values, Impact) Modern typography and a well-structured layout
Nice to have
• forest green, grey, white, black
Should not have
• references to marijuana, leafs, plants, or related product

```html
<!DOCTYPE html>
<html lang="en">
<head>
<meta charset="utf-8">
<title>Pavrel.com Business Card</title>
<link rel="stylesheet" href="https://fonts.googleapis.com/css2?family=Montserrat:wght@300;400;500;600;800&display=swap">
<style>
  :root {
    --backdrop: #3b3b3d;
    --card-white: #ffffff;
    --card-dark: #232323;
    --band-dark: #262626;
    --forest: #2f9a34;
    --logo-green: #173618;
    --ink-teal: #123238;
    --ink-grey: #3a3a3a;
    --back-mark: #1a1a1a;
  }
  * { margin: 0; padding: 0; box-sizing: border-box; }
  html, body { width: 1200px; height: 1200px; overflow: hidden; }
  body {
    background: var(--backdrop);
    font-family: "Montserrat", sans-serif;
    position: relative;
  }
  .card {
    position: absolute;
    left: 180px;
    width: 840px;
    height: 480px;
    border-radius: 36px;
    overflow: hidden;
  }
  .card-front {
    top: 80px;
    background: var(--card-white);
    border-bottom: 4px solid var(--forest);
  }
  .card-back {
    top: 640px;
    background: var(--card-dark);
    border: 3px solid var(--forest);
    display: flex;
    align-items: center;
    justify-content: center;
  }
  .front-bands { position: absolute; inset: 0; width: 100%; height: 100%; }
  .brand-name {
    position: absolute;
    top: 120px;
    right: 90px;
    font-weight: 800;
    font-size: 84px;
    letter-spacing: 2px;
    color: var(--logo-green);
  }
  .contact-block {
    position: absolute;
    left: 56px;
    top: 236px;
    color: var(--ink-teal);
  }
  .person-name {
    font-weight: 600;
    font-size: 44px;
    line-height: 1;
    letter-spacing: 1px;
  }
  .person-title {
    font-weight: 400;
    font-size: 28px;
    color: var(--ink-grey);
    margin: 6px 0 14px;
    letter-spacing: 1px;
  }
  .contact-line {
    display: flex;
    align-items: center;
    gap: 12px;
    font-size: 28px;
    font-weight: 400;
    color: var(--ink-grey);
    line-height: 1.3;
  }
  .contact-line svg { width: 26px; height: 26px; fill: var(--ink-teal); }
  .website {
    position: absolute;
    right: 56px;
    bottom: 52px;
    color: #ffffff;
    font-size: 24px;
    font-weight: 400;
    letter-spacing: 1px;
  }
  .back-name {
    font-weight: 800;
    font-size: 130px;
    letter-spacing: 4px;
    color: var(--back-mark);
  }
</style>
</head>
<body>
  <section class="card card-front">
    <svg class="front-bands" viewBox="0 0 840 480" preserveAspectRatio="none" aria-hidden="true">
      <path d="M0,440 H470 V458 H0 Z" fill="var(--forest)"/>
      <path d="M0,458 H460 C520,458 500,370 580,370 H840 V480 H0 Z" fill="var(--band-dark)"/>
    </svg>
    <div class="brand-name">PAVREL</div>
    <div class="contact-block">
      <div class="person-name">FULL NAME</div>
      <div class="person-title">TITLE</div>
      <div class="contact-line">
        <svg viewBox="0 0 24 24"><path d="M6.6 10.8a15.1 15.1 0 0 0 6.6 6.6l2.2-2.2a1 1 0 0 1 1-.25 11.4 11.4 0 0 0 3.6.57 1 1 0 0 1 1 1V20a1 1 0 0 1-1 1A17 17 0 0 1 3 4a1 1 0 0 1 1-1h3.5a1 1 0 0 1 1 1c0 1.25.2 2.45.57 3.57a1 1 0 0 1-.25 1z"/></svg>
        <span>(000) 000 0000</span>
      </div>
      <div class="contact-line">
        <svg viewBox="0 0 24 24"><path d="M2 5h20v14H2z M3.5 6.5 12 13l8.5-6.5" fill="none" stroke="var(--ink-teal)" stroke-width="2.2"/></svg>
        <span>email@company.com</span>
      </div>
    </div>
    <div class="website">www.company.com</div>
  </section>

  <section class="card card-back">
    <div class="back-name">PAVREL</div>
  </section>
</body>
</html>
```